-Photo booth rental Web Design Project

Our business is a small photo booth rental service serving the capital region and surrounding areas. The photo booth is a portable booth that fits up to 10 guest. I am looking for a website that will have social media capabilities and also private log ins for clients to view their photo albums online after their event. We provide full service photo booth rentals for all types of parties. I am looking for something fun and unique but also professional and I am also looking to maybe somehow incorporate the age of the photo booth which was invented in 1888. I do not have the photos of our photo booth available because we are just starting up and I wanted to get everything together first but I will provide stock photo booth pictures .Thank you for your patience i know it wont be an easy task with out those things. I added a word document describing information i will need on our website, i am looking for a home page, contact us and book an event page, online gallery page, and pricing. If you need any more information please feel free to contact me. Thanks for your help and I look forward to working with you.

Target Market(s)

For everyone from brides to be for their weddings or private parties, corporate parties, school dances, charity events, community events ect

Industry/Entity Type

Business

Requirements
Nice to have
• social media sharing

```html
<!DOCTYPE html>
<html lang="en">
<head>
<meta charset="utf-8">
<title>Giggle Frame Photo Booth</title>
<link href="https://fonts.googleapis.com/css2?family=Roboto:wght@300;400;500&family=Roboto+Condensed:wght@400;700&family=Roboto+Slab:wght@400;700&display=swap" rel="stylesheet">
<style>
:root{
  --backdrop:#8c7458;
  --page:#ffffff;
  --ink:#2b2b2b;
  --brown-dark:#3c2417;
  --brown-mid:#5a3a28;
  --brown-soft:#8b6f4e;
  --panel:#efeff0;
  --rule:#d9d9d9;
  --orange:#e8682a;
  --slate:#4c5d6c;
  --sky:#2aa6c8;
  --accent:#f07a2a;
}
*{box-sizing:border-box;margin:0;padding:0}
html,body{width:733px;height:1200px;overflow:hidden}
body{background:var(--backdrop);font-family:"Roboto",sans-serif;color:var(--ink);position:relative}
.page{position:absolute;left:94px;top:5px;width:547px;height:1174px;background:var(--page);border-top:3px solid #2a1a12}
.abs{position:absolute}
/* header */
.brand{left:6px;top:8px;font-family:"Roboto Condensed",sans-serif;font-weight:400;color:var(--brown-mid);font-size:22px;line-height:20px;letter-spacing:-.5px;display:flex;align-items:center;gap:6px}
.brand .mark{width:12px;height:12px;background:var(--brown-mid)}
.brand small{display:block;font-size:18px;padding-left:30px}
.nav{right:92px;top:26px;display:flex;font-family:"Roboto Condensed",sans-serif;font-size:8.5px;text-transform:uppercase}
.nav a{color:var(--ink);text-decoration:none;padding:0 6px;border-right:1px solid #bbb;line-height:20px}
.nav a:last-child{border:none}
.login{left:474px;top:22px;width:68px;height:20px;background:#2a1a12;color:#fff;font-family:"Roboto Condensed",sans-serif;font-size:7.5px;display:flex;align-items:center;justify-content:center;gap:4px}
.login i{width:5px;height:6px;background:#fff;border-radius:1px;display:inline-block}
/* hero */
.hero{left:4px;top:55px;width:540px;height:316px;background:linear-gradient(90deg,#2f3a2c 0%,#4d4a3e 45%,#5b4d4e 70%,#3e3a34 100%)}
.hero-photo{left:0;top:0;width:260px;height:316px;background:linear-gradient(180deg,#38402f,#5c4a3f)}
.hero h1{left:290px;top:62px;font-weight:300;font-size:25px;line-height:26px;color:#fff}
.hero p{left:290px;top:116px;width:205px;font-weight:300;font-size:8.5px;line-height:14px;color:#e6e6e6}
.hero .more{left:291px;top:173px;width:61px;height:25px;border:1.5px solid #fff;color:#fff;font-size:8px;display:flex;align-items:center;justify-content:center}
.dots{left:482px;top:302px;display:flex;gap:2px}
.dots span{width:10px;height:10px;border:1.5px solid #fff;border-radius:50%}
.dots span.on{background:radial-gradient(#fff 35%,transparent 40%)}
/* welcome */
.welcome{left:4px;top:375px;width:540px;height:103px;background:var(--panel)}
.welcome h2{left:11px;top:13px;font-family:"Roboto Slab",serif;font-weight:400;font-size:9px}
.welcome p{left:11px;top:30px;width:360px;font-size:7px;line-height:12.3px}
.welcome .shot{left:376px;top:10px;width:153px;height:83px;background:linear-gradient(90deg,#c22 0%,#b31a1a 45%,#2a2a2a 60%,#e9e9e9 80%,#333 100%);border:1px solid #bbb}
/* services */
.services-btn{left:238px;top:491px;width:72px;height:26px;border:1.5px solid var(--brown-mid);font-size:10px;letter-spacing:.5px;display:flex;align-items:center;justify-content:center;color:var(--brown-mid)}
.services-txt{left:60px;top:523px;width:427px;text-align:center;font-size:8px;line-height:13px;color:#444}
.arrows{left:256px;top:552px;display:flex;gap:2px}
.arrows span{width:18px;height:18px;background:var(--brown-soft);display:flex;align-items:center;justify-content:center}
.tile{top:578px;width:131px;height:95px;display:flex;align-items:center;justify-content:center}
.tile b{background:rgba(40,30,25,.8);color:#fff;font-family:"Roboto Slab",serif;font-size:7.5px;padding:5px 6px}
/* pricing */
.pricing{left:4px;top:681px;width:540px;height:373px;background:var(--brown-dark)}
.intro{left:21px;top:30px;width:153px;height:308px;background:linear-gradient(90deg,#fff 60%,#ececec)}
.intro .ico{left:56px;top:60px;width:41px;height:41px;border:2px solid var(--brown-soft);border-radius:50%;display:flex;align-items:center;justify-content:center}
.intro h3{left:0;width:153px;top:144px;text-align:center;font-family:"Roboto Slab",serif;font-weight:700;font-size:9.5px;color:#444}
.intro h3 span{color:var(--brown-soft)}
.intro .tier{left:0;width:153px;top:162px;text-align:center;font-family:"Roboto Condensed",sans-serif;font-weight:700;font-size:7px}
.deal{left:8px;top:216px;width:136px;height:70px;background:var(--brown-dark);color:#fff;text-align:center;font-family:"Roboto Slab",serif;font-size:7.5px;line-height:11px;padding-top:8px}
.deal .big{font-family:"Roboto",sans-serif;font-size:10px;margin-top:4px}
.deal .big em{font-style:normal;color:var(--accent);font-size:13px}
.col{background:#fff}
.col.std{left:174px;top:19px;width:115px;height:342px;background:linear-gradient(90deg,#fff,#f4f4f4)}
.col.ult{left:289px;top:12px;width:115px;height:358px;background:linear-gradient(90deg,#d9d9dc,#e9e9ea)}
.col.ext{left:404px;top:16px;width:114px;height:345px;background:linear-gradient(90deg,#fff 70%,#eee)}
.tab{height:24px;color:#fff;font-family:"Roboto Slab",serif;font-weight:700;font-size:8px;display:flex;align-items:center;justify-content:center;letter-spacing:.4px}
.tab.orange{left:21px;top:7px;width:63px;background:var(--orange)}
.tab.slate{left:22px;top:0;width:63px;background:var(--slate)}
.tab.sky{left:23px;top:4px;width:65px;background:var(--sky)}
ul.feat{position:absolute;left:10px;width:95px;list-style:none;font-family:"Roboto Condensed",sans-serif;font-size:7px}
ul.feat li{padding:5.5px 0 5px 10px;border-bottom:1px solid var(--rule);line-height:10px;position:relative}
ul.feat li:last-child{border:none}
ul.feat li::before{content:"";position:absolute;left:0;top:9px;width:3.5px;height:3.5px;border-radius:50%;background:#777}
ul.feat li span{color:var(--accent)}
/* footer */
.foot{left:0;top:1062px;width:547px;height:112px;background:var(--panel)}
.foot h4{top:20px;font-family:"Roboto Slab",serif;font-weight:400;font-size:8px}
.email{left:11px;top:31px;width:206px;height:22px;border:1px solid #aaa;background:#e8e8e8;display:flex}
.email span{flex:1;font-size:7px;padding:7px 8px;color:#555}
.email i{width:23px;border-left:1px solid #aaa;display:flex;align-items:center;justify-content:center}
.social{left:462px;top:32px;display:flex;gap:5px}
.social span{width:14px;height:14px}
.foot hr{position:absolute;left:11px;top:66px;width:525px;border:none;border-top:1px solid #ccc}
.links{left:0;width:547px;top:79px;text-align:center;font-size:7px;color:#444}
.copy{left:0;width:547px;top:92px;text-align:center;font-size:7px;color:#444}
</style>
</head>
<body>
<div class="page">
  <header>
    <div class="abs brand"><div><span>Giggle Frame</span><small>photo booth</small></div><span class="mark"></span></div>
    <nav class="abs nav"><a>Home</a><a>Pricing</a><a>Contact us</a><a>Book an event</a><a>Gallery</a></nav>
    <div class="abs login"><i></i>CLIENT LOG IN</div>
  </header>

  <section class="abs hero">
    <div class="abs hero-photo" role="img" aria-label="Couple posing beside a red and black photo booth"></div>
    <h1 class="abs">Photo Booth<br>Rental</h1>
    <p class="abs">Lorem Ipsum is simply dummy text of the printing and typesetting industry Contrary to popular belief, Lorem Ipsum</p>
    <div class="abs more">READ MORE</div>
    <div class="abs dots"><span></span><span class="on"></span><span></span><span></span></div>
  </section>

  <section class="abs welcome">
    <h2 class="abs">WELCOME TO OUR SITE</h2>
    <p class="abs">There are many variations of passages of Lorem Ipsum available, but the majority have suffered alteration in some form, by injected humour, or randomised words which don't look even slightly believable. If you are going to use a passage of Lorem Ipsum, you need to be sure there isn't anything embarrassing hidden in the middle of text. All the Lorem Ipsum generators on the Internet tend to repeat predefined chunks as necessary,</p>
    <div class="abs shot" role="img" aria-label="Photo booth interior with red curtain and photo strips"></div>
  </section>

  <div class="abs services-btn">SERVICES</div>
  <p class="abs services-txt">The standard chunk of Lorem Ipsum used since the 1500s is reproduced below for those interested.Sections 1.10.32 and 1.10.33 from "de Finibus Bonorum et Malorum</p>
  <div class="abs arrows">
    <span><svg width="8" height="10"><path d="M6 1L2 5l4 4" stroke="#fff" stroke-width="1.6" fill="none"/></svg></span>
    <span><svg width="8" height="10"><path d="M2 1l4 4-4 4" stroke="#fff" stroke-width="1.6" fill="none"/></svg></span>
  </div>
  <div class="abs tile" style="left:5px;background:linear-gradient(135deg,#7a4a2e,#c9b9a6 60%,#5a4636)" role="img" aria-label="Wedding couple with bouquet"><b>WEDDINGS</b></div>
  <div class="abs tile" style="left:140px;background:linear-gradient(135deg,#2a3f7a,#c8643a 55%,#e9c47a)" role="img" aria-label="Children with birthday cake"><b>BIRTHDAY PARTIES</b></div>
  <div class="abs tile" style="left:276px;background:linear-gradient(160deg,#4a8ad0,#9cc2e8 45%,#2d3e6a)" role="img" aria-label="Graduates throwing caps"><b>GRADUATIONS</b></div>
  <div class="abs tile" style="left:411px;background:linear-gradient(135deg,#3a2a26,#b23a2a 50%,#e8ddd3)" role="img" aria-label="Holiday toast with glasses"><b>HOLIDAY PARTIES</b></div>

  <section class="abs pricing">
    <div class="abs intro">
      <div class="abs ico"><svg width="18" height="16"><rect x="1" y="4" width="16" height="11" rx="1.5" fill="#4a4a4a"/><rect x="4" y="1" width="10" height="5" fill="#4a4a4a"/><rect x="6" y="8" width="6" height="2" fill="#fff"/></svg></div>
      <h3 class="abs">PRICING <span>INFORMATION</span></h3>
      <div class="abs tier">3 TIER PACKAGES</div>
      <div class="abs deal">MAGNET PHOTO STRIP FRAMES,<br>STAND UP ACRYLICPHOTO<br>STRIP FRAMES,<div class="big">ONLY <em>$100</em> deposit</div></div>
    </div>
    <div class="abs col std">
      <div class="abs tab orange">STANDARD</div>
      <ul class="feat" style="top:43px">
        <li>3 Hours of Service</li><li>Set up &amp; Removal</li><li>Professional &amp; friendly booth attendant</li><li>DVD or usb flash drive of picture</li><li>Guestbook</li><li>Unlimited Prints</li><li>Online Gallery</li><li>Digital Backdrop <span>$675</span></li>
      </ul>
    </div>
    <div class="abs col ult">
      <div class="abs tab slate">ULTIMATE</div>
      <ul class="feat" style="top:43px">
        <li>4 hours of service</li><li>Set up &amp; Removal</li><li>Professional &amp; friendly booth attendant</li><li>DVDor usb flash drive of picture gallery</li><li>Guestbook</li><li>Unlimited Prints</li><li>Custom Backdrop</li><li>Video Messaging</li><li>Props Package</li><li>Instant Social Media Uploads</li><li>Digital Backdrop <span>$850</span></li>
      </ul>
    </div>
    <div class="abs col ext">
      <div class="abs tab sky">EXTREME</div>
      <ul class="feat" style="top:39px">
        <li>5 hours of service</li><li>Set up &amp; Removal</li><li>Professional &amp; friendly booth attendant</li><li>DVDor usb flash drive of picture gallery</li><li>Guestbook</li><li>Unlimited Prints</li><li>Custom Backdrop</li><li>Video Messaging</li><li>Props Package</li><li>Online Gallery</li><li>Red Carpet Event</li><li>Instant Social Media Uploads</li><li>Digital Backdrop <span>$850</span></li>
      </ul>
    </div>
  </section>

  <footer class="abs foot">
    <h4 class="abs" style="left:11px">NEWSLETTER</h4>
    <h4 class="abs" style="right:11px">FOLLOW</h4>
    <div class="abs email"><span>E mail</span><i><svg width="8" height="10"><path d="M2 1l4 4-4 4" stroke="#555" stroke-width="1.6" fill="none"/></svg></i></div>
    <div class="abs social"><span style="background:#3b5a9a"></span><span style="background:#2fa3dc"></span><span style="background:#1a78b4"></span><span style="background:#c8302a"></span></div>
    <hr>
    <p class="abs links">Home | &nbsp;Pricing | &nbsp;Contact us | &nbsp;Book an event | &nbsp;Client log in</p>
    <p class="abs copy">Copyrights @2014 All Rights Reserved</p>
  </footer>
</div>
</body>
</html>
```